Wildlfower Field Guide Needs a Book Cover Design

We need a book cover design in formats compatible with Adobe Illustrator and/or Photoshop (vector file that can be edited). I have attached a Power Point file with the general design features for the front and back covers and photographs to be used in the book cover. The cover size is 6" wide by 9" high (same size as the attached Power Point file). The book cover should have the same format including photos as the attached file with a similar color scheme. We are looking for a sky blue background then title text in a complementary darker blue. The other color elements (borders around photos) can be the same darker blue or dark gray. We are looking for better text types/styles for the title than those is the attached file. All three lines of the title should have the same width (1st line - thicker text, 2nd line - white italics on dark background, 3rd line - narrow text). The dark background on the 2nd line would ideally have some texture or style like a trail. On the back cover, written paragraphs should remain in Ebrima font.

Requirements
Must have
• Project should follow general cover outline of attached Power Point file
• Should have desired color scheme
• Must include all photos as formatted in the attached in the Power point file
Nice to have
• The title (2nd line) can be a solid color matching 1st line text or texture like a hiking trail

```html
<!DOCTYPE html>
<html lang="en">
<head>
<meta charset="utf-8">
<title>Wild Blossoms Beside the Path – Book Cover</title>
<link rel="stylesheet" href="https://fonts.googleapis.com/css2?family=Outfit:wght@400;700&family=Nunito:ital,wght@1,600&family=Open+Sans:wght@400&display=swap">
<style>
  :root {
    --page-bg: #ffffff;
    --sky: #c9def0;
    --title-blue: #1a6db5;
    --band-blue: #1a6db5;
    --band-text: #ffffff;
    --frame-gray: #3b3e39;
    --grid-line: #e6e6e6;
  }
  html, body {
    margin: 0;
    width: 1200px;
    height: 1141px;
    overflow: hidden;
    background: var(--page-bg);
  }
  .book-cover {
    position: absolute;
    left: 250px;
    top: 45px;
    width: 700px;
    height: 1050px;
    display: block;
  }
  .cover-bg { fill: var(--sky); }
  .title-main {
    font-family: "Outfit", sans-serif;
    font-weight: 700;
    font-size: 74px;
    fill: var(--title-blue);
  }
  .title-band { fill: var(--band-blue); }
  .title-band-text {
    font-family: "Nunito", sans-serif;
    font-weight: 600;
    font-style: italic;
    font-size: 60px;
    fill: var(--band-text);
  }
  .title-region {
    font-family: "Outfit", sans-serif;
    font-weight: 400;
    font-size: 46px;
    fill: var(--title-blue);
  }
  .photo-frame { fill: var(--frame-gray); }
  .grid-line { stroke: var(--grid-line); stroke-width: 2; }
  .author {
    font-family: "Open Sans", sans-serif;
    font-weight: 400;
    font-size: 46px;
    fill: var(--title-blue);
  }
</style>
</head>
<body>
<svg class="book-cover" viewBox="0 0 700 1050" xmlns="http://www.w3.org/2000/svg">
  <defs>
    <radialGradient id="bloom" cx="50%" cy="50%" r="60%">
      <stop offset="0%" stop-color="#f0d43a"/>
      <stop offset="45%" stop-color="#e6c624"/>
      <stop offset="75%" stop-color="#6a6a52"/>
      <stop offset="100%" stop-color="#3f4238"/>
    </radialGradient>
    <radialGradient id="bloom-daisy" cx="50%" cy="50%" r="60%">
      <stop offset="0%" stop-color="#e9a923"/>
      <stop offset="30%" stop-color="#f2cf1e"/>
      <stop offset="70%" stop-color="#8a8766"/>
      <stop offset="100%" stop-color="#5c5d52"/>
    </radialGradient>
  </defs>

  <rect class="cover-bg" x="0" y="0" width="700" height="1050"/>

  <text class="title-main" x="75" y="140" textLength="556" lengthAdjust="spacingAndGlyphs">WILD BLOSSOMS</text>

  <rect class="title-band" x="75" y="155" width="556" height="78"/>
  <text class="title-band-text" x="92" y="213" textLength="522" lengthAdjust="spacingAndGlyphs">Beside the Path</text>

  <text class="title-region" x="75" y="287" textLength="556" lengthAdjust="spacingAndGlyphs">A Sonoran Desert Guide</text>

  <g class="photo-grid">
    <rect class="photo-frame" x="76" y="342" width="564" height="584"/>
    <g role="img" aria-label="Nine close-up photographs of yellow desert wildflowers">
      <rect x="81" y="347" width="184" height="190" fill="url(#bloom)"/>
      <rect x="266" y="347" width="184" height="190" fill="url(#bloom)"/>
      <rect x="451" y="347" width="184" height="190" fill="url(#bloom)"/>
      <rect x="81" y="538" width="184" height="190" fill="url(#bloom)"/>
      <rect x="266" y="538" width="184" height="190" fill="url(#bloom)"/>
      <rect x="451" y="538" width="184" height="190" fill="url(#bloom)"/>
      <rect x="81" y="729" width="184" height="192" fill="url(#bloom-daisy)"/>
      <rect x="266" y="729" width="184" height="192" fill="url(#bloom-daisy)"/>
      <rect x="451" y="729" width="184" height="192" fill="url(#bloom-daisy)"/>
    </g>
    <line class="grid-line" x1="265.5" y1="347" x2="265.5" y2="921"/>
    <line class="grid-line" x1="450.5" y1="347" x2="450.5" y2="921"/>
    <line class="grid-line" x1="81" y1="537.5" x2="635" y2="537.5"/>
    <line class="grid-line" x1="81" y1="728.5" x2="635" y2="728.5"/>
  </g>

  <text class="author" x="360" y="988" text-anchor="middle">Daniel Hartwell</text>
</svg>
</body>
</html>
```